Brookvane Consulting Business Card Design

Business Card Design for Brookvane Consulting. Brookvane Consulting is a boutique consultancy based in Atlanta, GA., that specializes in marketing strategy, organization planning, and leadership development. We provide solutions for small businesses and startups as well as Vantage 300 companies.

http://brookvaneconsulting.com/

Target Market(s)

We provide solutions for small businesses and startups as well as Vantage 300 companies.

Industry/Entity Type

Consulting

Contact Information for Business Card

Two sided business card with priority on contact information, logo, tag line (Guidance to think bigger, act bolder, grow further)

Colors

Designer to choose colors to be used in the design.

Requirements
Must have
• contact information, logo, tag line (Guidance to think bigger, act bolder, grow further)
• Simple no over communication.
Nice to have
• I would like to see different placements of logo and creative use of both sides of the card
Should not have
• Do not put too much information on the card.

```html
<!DOCTYPE html>
<html lang="en">
<head>
<meta charset="utf-8">
<title>Brookvane Consulting Business Card</title>
<link rel="stylesheet" href="https://fonts.googleapis.com/css2?family=Mulish:wght@400;600;700&display=swap">
<style>
  :root {
    --page: #e9e6e1;
    --card-white: #ffffff;
    --card-black: #050505;
    --band-black: #111214;
    --texture-dark: #1a1b1d;
    --texture-mid: #3a3b3e;
    --ink: #111111;
    --paper-text: #f2f2f2;
    --muted-text: #cfcfcf;
  }
  * { margin: 0; padding: 0; box-sizing: border-box; }
  html, body {
    width: 1200px; height: 900px; overflow: hidden;
    background: var(--page);
    font-family: "Mulish", Arial, sans-serif;
  }
  .canvas {
    position: relative; width: 1200px; height: 900px;
    display: flex; flex-direction: column; align-items: center; justify-content: center; gap: 40px;
  }
  .card {
    position: relative; width: 700px; height: 400px; overflow: hidden;
    box-shadow: 0 6px 18px rgba(0,0,0,0.18);
  }

  /* Contact side */
  .card--contact { background: var(--card-white); }
  .contact-band {
    position: absolute; left: 0; right: 0; bottom: 0; height: 150px;
    background: var(--band-black);
  }
  .contact-band__texture {
    position: absolute; top: 0; right: 0; bottom: 0; width: 62%;
    background: linear-gradient(90deg, var(--band-black) 0%, var(--texture-dark) 40%, var(--texture-mid) 75%, var(--texture-dark) 100%);
  }
  .brand-block { position: absolute; left: 48px; bottom: 168px; color: var(--ink); }
  .brand-name {
    font-weight: 700; font-size: 40px; letter-spacing: 0.5px; line-height: 1;
  }
  .brand-name__small {
    display: block; font-size: 17px; font-weight: 600; letter-spacing: 4px; margin-top: 6px;
  }
  .tagline { margin-top: 12px; font-size: 16px; font-weight: 600; }
  .contact-list {
    position: absolute; left: 48px; bottom: 28px; list-style: none;
    color: var(--paper-text); font-size: 14px; letter-spacing: 2px;
  }
  .contact-list li { display: flex; align-items: center; gap: 14px; height: 30px; }
  .contact-list svg { width: 18px; height: 18px; fill: none; stroke: var(--paper-text); stroke-width: 1.6; flex: none; }

  /* Logo side */
  .card--logo { background: var(--card-black); }
  .logo-side__texture {
    position: absolute; top: 0; left: 0; bottom: 0; width: 60%;
    background: radial-gradient(ellipse 90% 110% at 0% 70%, var(--texture-mid) 0%, var(--texture-dark) 45%, var(--card-black) 100%);
  }
  .logo-side__brand {
    position: absolute; right: 70px; top: 50%; transform: translateY(-50%);
    color: var(--paper-text);
  }
  .logo-side__brand .brand-name { font-size: 48px; }
  .logo-side__brand .brand-name__small { font-size: 20px; color: var(--muted-text); }
</style>
</head>
<body>
<main class="canvas">
  <section class="card card--contact" aria-label="Business card, contact side">
    <div class="brand-block">
      <p class="brand-name">Brookvane<span class="brand-name__small">CONSULTING</span></p>
      <p class="tagline">Guidance to think bigger, act bolder, grow further</p>
    </div>
    <div class="contact-band">
      <div class="contact-band__texture" role="img" aria-label="Dark curved geometric texture"></div>
      <ul class="contact-list">
        <li>
          <svg viewBox="0 0 18 18"><rect x="1.5" y="4" width="15" height="10"/><path d="M1.5 4 L9 10 L16.5 4"/></svg>
          DANA@BROOKVANECONSULTING.COM
        </li>
        <li>
          <svg viewBox="0 0 18 18"><path d="M4 2 L7 2 L8 6 L6 7.5 Q7.5 10.5 10.5 12 L12 10 L16 11 L16 14 Q9 16 4 10 Q2 6 4 2 Z"/></svg>
          555-014-2290
        </li>
        <li>
          <svg viewBox="0 0 18 18"><circle cx="9" cy="9" r="7.5"/><ellipse cx="9" cy="9" rx="3.2" ry="7.5"/><path d="M1.5 9 H16.5 M3 5 H15 M3 13 H15"/></svg>
          HTTP://BROOKVANECONSULTING.COM/HOME.HTML
        </li>
      </ul>
    </div>
  </section>

  <section class="card card--logo" aria-label="Business card, logo side">
    <div class="logo-side__texture" role="img" aria-label="Dark curved geometric texture"></div>
    <div class="logo-side__brand">
      <p class="brand-name">Brookvane<span class="brand-name__small">CONSULTING</span></p>
    </div>
  </section>
</main>
</body>
</html>
```